we can communicate on this, but i want to follow the approach we took on Pellew|Marsh & Quinlan but i feel the card front needs the black background and the platinum and gold logo. The back? I am open. we can use the same info from PM&Q. Velmont Arc is an enhanced equity investment fund - basically a very exclusive boutique hedge fund that uses only stock options. very advanced things. hope you are interested

Contact Information for Business Card

Dr. Lewis T. Brennick, CFA
Scientifique de fusée financière
701.555.0143
LTBquant47@mailvantor.com

4718 Willow Creek Bend W.
West Fargo, ND 58078

No web site

Colors

Designer to choose colors to be used in the design.

Requirements
Nice to have
• I tend to prefer the most visible applications of the logo to include logo and name, the logo version with a black background and the gold and platinum components separated by the black. I see this working well for a single side (logo and name - this is card front to me).
• I am fairly open to other treatments on the reverse side with the data. To me, it makes sense to have a different color rendition of the logo on the reverse and it may be a muted black tone on tone or an oversized portion that would have spot UV. Or, the reverse may play with colors and layout
Should not have
• Other colors = no no
• Decorative font

```html
<!DOCTYPE html>
<html lang="en">
<head>
<meta charset="utf-8">
<title>Velmont Arc – Business Card</title>
<link rel="stylesheet" href="https://fonts.googleapis.com/css2?family=Arimo:wght@400;700&family=Montserrat:wght@600&display=swap">
<style>
  :root {
    --backdrop: #d9d4cc;
    --card-top: #1c1c1d;
    --card-bottom: #0a0a0b;
    --platinum: #e5e4e2;
    --platinum-soft: rgba(229,228,226,0.10);
    --gold: #b08a3a;
    --gold-light: #d6b46a;
    --gold-dark: #7a5a1c;
    --rule: #cfcdca;
  }
  * { box-sizing: border-box; margin: 0; padding: 0; }
  html, body {
    width: 1200px; height: 970px; overflow: hidden;
    background: var(--backdrop);
  }
  .card {
    position: absolute; left: 100px; top: 201px;
    width: 1000px; height: 568px;
    border-radius: 26px; overflow: hidden;
    background: linear-gradient(160deg, var(--card-top) 0%, #131314 55%, var(--card-bottom) 100%);
    box-shadow: 0 18px 40px rgba(0,0,0,0.28);
    font-family: "Arimo", Arial, sans-serif;
    color: var(--platinum);
  }
  .card__halo {
    position: absolute; left: 580px; top: -20px;
    width: 420px; height: 420px; border-radius: 50%;
    border: 6px solid var(--platinum-soft);
  }
  .brand {
    position: absolute; left: 55px; top: 62px;
    width: 330px; text-align: center;
  }
  .brand__dot {
    display: block; margin: 0 auto 28px;
    width: 150px; height: 150px; border-radius: 50%;
    background: var(--gold);
  }
  .brand__name {
    font-family: "Montserrat", sans-serif; font-weight: 600;
    font-size: 46px; line-height: 1.05; letter-spacing: 1px;
    color: var(--platinum); text-transform: uppercase;
  }
  .holder {
    position: absolute; right: 54px; top: 91px; text-align: right;
  }
  .holder__name { font-weight: 700; font-size: 32px; letter-spacing: 0.5px; text-transform: uppercase; }
  .holder__role { font-size: 24px; color: var(--gold-light); margin-top: 4px; }
  .card__rule {
    position: absolute; left: 58px; right: 54px; top: 413px;
    height: 2px; background: var(--rule);
  }
  .contact {
    position: absolute; left: 58px; top: 432px; list-style: none;
    font-size: 23px;
  }
  .contact__item { display: flex; align-items: center; height: 38px; }
  .contact__icon { width: 24px; height: 24px; margin-right: 14px; flex: none; }
  .address {
    position: absolute; right: 54px; top: 432px; text-align: right;
    font-size: 23px; line-height: 33px;
  }
  .card__edge {
    position: absolute; left: 0; right: 0; bottom: 0; height: 12px;
    background: linear-gradient(90deg, var(--gold-dark), var(--gold-light) 40%, var(--gold) 70%, var(--gold-dark));
  }
</style>
</head>
<body>
  <main class="card">
    <div class="card__halo"></div>

    <div class="brand">
      <span class="brand__dot"></span>
      <p class="brand__name">Velmont<br>Arc</p>
    </div>

    <div class="holder">
      <p class="holder__name">Dr. Lewis T. Brennick, CFA</p>
      <p class="holder__role">Scientifique de fusée financière</p>
    </div>

    <div class="card__rule"></div>

    <ul class="contact">
      <li class="contact__item">
        <svg class="contact__icon" viewBox="0 0 24 24"><circle cx="12" cy="12" r="12" fill="#b08a3a"/><path d="M8.5 6.5c.6-.4 1.3-.2 1.6.4l1 1.8c.3.5.1 1.1-.3 1.4l-.8.6c.6 1.4 1.6 2.5 3 3.2l.6-.8c.3-.4 1-.6 1.4-.3l1.8 1c.6.3.8 1 .4 1.6-.7 1-1.8 1.6-3 1.2-3.3-1-5.9-3.6-6.9-6.9-.3-1.2.2-2.4 1.2-3.2z" fill="#111"/></svg>
        701.555.0143
      </li>
      <li class="contact__item">
        <svg class="contact__icon" viewBox="0 0 24 24"><circle cx="12" cy="12" r="12" fill="#b08a3a"/><rect x="6" y="8" width="12" height="8" fill="#111"/><path d="M6 8l6 5 6-5" fill="none" stroke="#b08a3a" stroke-width="1.2"/></svg>
        LTBquant47@mailvantor.com
      </li>
    </ul>

    <div class="address">
      <p>4718 Willow Creek Bend W.</p>
      <p>West Fargo, ND 58078</p>
    </div>

    <div class="card__edge"></div>
  </main>
</body>
</html>
```